Business Card for Coastal Tundrabridge Advisory

We need a business card for Coastal Tundrabridge Advisory. The company website address is provided below. The company logo is attached. We provide specialized permafrost services to the mining, transportation, and oil & gas industries. The card should be prepared for:
Matthias Korhonen, PhD.
Coastal Tundrabridge Advisory
PO Box 418259
Quillwater, Alaska 99642
Direct: +1-907-555-0143
Email: mkorhonen@tundrabridgeadvisory.example
Website: www.coastaltundrabridgeadvisory.example

```html
<!DOCTYPE html>
<html lang="en">
<head>
<meta charset="utf-8">
<title>Coastal Tundrabridge Advisory – Business Card</title>
<link rel="stylesheet" href="https://fonts.googleapis.com/css2?family=Poppins:wght@300;600&family=Roboto:wght@400;500;700&display=swap">
<style>
  :root {
    --backdrop: #232323;
    --paper: #ffffff;
    --ink: #14171c;
    --navy-deep: #0b111b;
    --navy: #1a2433;
    --navy-light: #2a3646;
    --frost: #f2f4f7;
    --frost-soft: #c9d0da;
  }
  * { box-sizing: border-box; margin: 0; padding: 0; }
  html, body { width: 1200px; height: 780px; overflow: hidden; }
  body {
    background: var(--backdrop);
    display: flex;
    align-items: center;
    justify-content: center;
    gap: 40px;
    font-family: "Roboto", sans-serif;
  }
  .card {
    width: 540px;
    height: 309px;
    position: relative;
    overflow: hidden;
    box-shadow: 0 14px 30px rgba(0,0,0,.45);
  }

  /* Front: contact side */
  .card-front { background: var(--paper); color: var(--ink); }
  .holder {
    position: absolute;
    left: 42px;
    top: 118px;
    font-family: "Poppins", sans-serif;
    font-size: 25px;
    line-height: 1;
    white-space: nowrap;
  }
  .holder-first { font-weight: 600; }
  .holder-last { font-weight: 300; }
  .holder-title {
    display: block;
    text-align: right;
    font-weight: 600;
    font-size: 13px;
    margin-top: 4px;
  }
  .divider {
    position: absolute;
    left: 300px;
    top: 92px;
    width: 1px;
    height: 96px;
    background: var(--ink);
  }
  .contacts {
    position: absolute;
    left: 316px;
    top: 98px;
    list-style: none;
    font-size: 10.5px;
    line-height: 1;
  }
  .contacts li {
    display: flex;
    align-items: center;
    gap: 6px;
    margin-bottom: 8px;
    white-space: nowrap;
  }
  .contact-icon { width: 12px; height: 12px; flex: none; }
  .address {
    position: absolute;
    left: 140px;
    bottom: 30px;
    font-size: 13px;
    letter-spacing: .2px;
    white-space: nowrap;
  }

  /* Back: brand side */
  .card-back { background: var(--navy-deep); color: var(--frost); }
  .pattern-field {
    position: absolute;
    inset: 0;
    background: linear-gradient(160deg, var(--navy-light) 0%, var(--navy) 40%, var(--navy-deep) 100%);
  }
  .brand-name {
    position: absolute;
    left: 0;
    right: 0;
    top: 92px;
    text-align: center;
    font-family: "Roboto", sans-serif;
    font-weight: 500;
    font-size: 29px;
    letter-spacing: 1px;
    color: var(--frost);
  }
  .services {
    position: absolute;
    left: 0;
    right: 0;
    bottom: 38px;
    text-align: center;
  }
  .services-title {
    font-weight: 700;
    font-size: 12px;
    letter-spacing: .4px;
    margin-bottom: 6px;
  }
  .services-text {
    font-size: 11.5px;
    color: var(--frost-soft);
  }
</style>
</head>
<body>
  <section class="card card-front" aria-label="Contact side">
    <div class="holder">
      <span class="holder-first">Matthias</span> <span class="holder-last">Korhonen</span>
      <span class="holder-title">PhD</span>
    </div>
    <div class="divider"></div>
    <ul class="contacts">
      <li>
        <svg class="contact-icon" viewBox="0 0 12 12" aria-hidden="true"><circle cx="6" cy="6" r="6" fill="#14171c"/><path d="M4 3.2c.4 0 .7.9.7 1.2s-.5.5-.4.8c.3.7.8 1.2 1.5 1.5.3.1.5-.4.8-.4s1.2.3 1.2.7-.5 1-1 1C4.9 8 3.8 6.9 3.2 5 3.1 4 3.5 3.2 4 3.2z" fill="#fff"/></svg>
        <span>+1-907-555-0143</span>
      </li>
      <li>
        <svg class="contact-icon" viewBox="0 0 12 12" aria-hidden="true"><circle cx="6" cy="6" r="6" fill="#14171c"/><rect x="3" y="4" width="6" height="4.2" fill="#fff"/><path d="M3 4l3 2.3L9 4" fill="none" stroke="#14171c" stroke-width=".7"/></svg>
        <span>mkorhonen@tundrabridgeadvisory.example</span>
      </li>
      <li>
        <svg class="contact-icon" viewBox="0 0 12 12" aria-hidden="true"><circle cx="6" cy="6" r="6" fill="#14171c"/><circle cx="6" cy="6" r="3.2" fill="none" stroke="#fff" stroke-width=".7"/><path d="M2.8 6h6.4M6 2.8c-1.5 1.8-1.5 4.6 0 6.4M6 2.8c1.5 1.8 1.5 4.6 0 6.4" fill="none" stroke="#fff" stroke-width=".6"/></svg>
        <span>www.coastaltundrabridgeadvisory.example</span>
      </li>
    </ul>
    <p class="address">PO Box 418259 Quillwater, Alaska 99642</p>
  </section>

  <section class="card card-back" aria-label="Brand side">
    <div class="pattern-field" role="img" aria-label="Dark navy field with a faint repeated company-name texture"></div>
    <p class="brand-name">Coastal Tundrabridge Advisory</p>
    <div class="services">
      <p class="services-title">OUR SERVICES</p>
      <p class="services-text">We provide specialized permafrost services to the mining, transportation, and oil &amp; gas industries</p>
    </div>
  </section>
</body>
</html>
```